Business cards for a fun web development agency

Hi,I am building a web development agency. You can read about it on the website http://kite-loft.examplehost.com. Basically, I want to focus on free and open source products and stay as far away from the corporate business feeling as possible. I want to build a community so I want the business card to feel fun and approachable (at the risk of professional if need be). I am uploading some of my image assets in various file formats. Feel free to use them or make your own if you want just keeping in theme with the website.
Industry/Entity Type
Building
Contact Information for Business Card
Company Name: Boat ShedWebsite: www.kiteloftdev.example (it's currently in alpha on http://kite-loft.examplehost.com if you want to see the them we are trying to capture)My name is: Banner B. SchaferMy email: banner@boatsheddev.comMy phone: 0431 587 904
Look and feel

```html
<!DOCTYPE html>
<html lang="en">
<head>
<meta charset="utf-8">
<title>Kite Loft — Business Cards</title>
<link rel="stylesheet" href="https://fonts.googleapis.com/css2?family=Josefin+Sans:wght@400;600;700&display=swap">
<style>
  :root {
    --bg: #e4e5e6;
    --card: #ffffff;
    --brand-blue: #1b86b9;
    --band-blue: #1c88bb;
    --wave-grey: #9a9c9f;
    --ink-light: #ffffff;
    --shadow: rgba(0, 0, 0, 0.18);
  }
  * { box-sizing: border-box; margin: 0; padding: 0; }
  html, body {
    width: 1200px;
    height: 771px;
    overflow: hidden;
    background: var(--bg);
    font-family: "Josefin Sans", sans-serif;
  }
  .canvas {
    position: relative;
    width: 1200px;
    height: 771px;
  }
  .card {
    position: absolute;
    top: 231px;
    width: 540px;
    height: 309px;
    background: var(--card);
    box-shadow: 0 6px 18px var(--shadow);
    overflow: hidden;
  }
  .card--front { left: 40px; }
  .card--back  { left: 620px; }

  .wordmark {
    display: flex;
    align-items: center;
    gap: 14px;
    color: var(--brand-blue);
    font-weight: 600;
    letter-spacing: 1px;
    white-space: nowrap;
  }
  .wordmark__dot {
    border-radius: 50%;
    background: var(--brand-blue);
    flex: none;
  }
  .card--front .wordmark {
    position: absolute;
    left: 0; right: 0; top: 0; bottom: 0;
    justify-content: center;
    font-size: 54px;
  }
  .card--front .wordmark__dot { width: 46px; height: 46px; }

  .card__waves {
    position: absolute;
    inset: 0;
    width: 540px;
    height: 309px;
  }
  .card--back .wordmark {
    position: absolute;
    left: 150px;
    top: 32px;
    font-size: 44px;
  }
  .card--back .wordmark__dot { width: 38px; height: 38px; }

  .contact {
    position: absolute;
    left: 40px;
    top: 168px;
    display: flex;
    color: var(--ink-light);
    font-size: 10px;
    letter-spacing: 1.4px;
    text-transform: uppercase;
  }
  .contact__person {
    width: 196px;
    text-align: right;
    padding-right: 14px;
    line-height: 16px;
  }
  .contact__name {
    font-weight: 700;
    font-size: 11px;
    letter-spacing: 2px;
  }
  .contact__role { margin-bottom: 10px; }
  .contact__divider {
    width: 1px;
    height: 96px;
    background: var(--ink-light);
    opacity: 0.8;
  }
  .contact__list {
    list-style: none;
    padding-left: 14px;
    line-height: 17px;
  }
  .contact__list li {
    display: flex;
    align-items: center;
    gap: 7px;
  }
  .contact__list .lower { text-transform: none; letter-spacing: 1px; }
  .contact__icon {
    width: 12px;
    height: 12px;
    flex: none;
  }
</style>
</head>
<body>
<main class="canvas">

  <section class="card card--front" aria-label="Card front">
    <div class="wordmark">
      <span>KITE</span>
      <span class="wordmark__dot" aria-hidden="true"></span>
      <span>LOFT</span>
    </div>
  </section>

  <section class="card card--back" aria-label="Card back">
    <svg class="card__waves" viewBox="0 0 540 309" aria-hidden="true">
      <path d="M0,104 C140,86 300,170 540,210 L540,309 L0,309 Z" fill="var(--wave-grey)"/>
      <path d="M0,120 C150,104 300,190 540,232 L540,309 L0,309 Z" fill="var(--band-blue)"/>
    </svg>

    <div class="wordmark">
      <span>KITE</span>
      <span class="wordmark__dot" aria-hidden="true"></span>
      <span>LOFT</span>
    </div>

    <div class="contact">
      <div class="contact__person">
        <p class="contact__name">Corwin T. Aldous</p>
        <p class="contact__role">Owner / C.E.O</p>
        <p>Suite # 14, Loft Bldg,</p>
        <p>NY 10442</p>
      </div>
      <span class="contact__divider" aria-hidden="true"></span>
      <ul class="contact__list">
        <li>
          <svg class="contact__icon" viewBox="0 0 12 12" aria-hidden="true"><circle cx="6" cy="6" r="6" fill="#fff"/><path d="M4,3 L5,3 L5.6,4.6 L4.9,5.2 Q5.6,6.6 6.8,7.1 L7.4,6.4 L9,7 L9,8 Q6,9 3.5,5 Q3.4,3.6 4,3 Z" fill="var(--band-blue)"/></svg>
          <span>0431 587 904</span>
        </li>
        <li>
          <svg class="contact__icon" viewBox="0 0 12 12" aria-hidden="true"><circle cx="6" cy="6" r="6" fill="#fff"/><rect x="4.2" y="2.6" width="3.6" height="6.8" rx="0.7" fill="var(--band-blue)"/></svg>
          <span>0431 587 905</span>
        </li>
        <li>
          <svg class="contact__icon" viewBox="0 0 12 12" aria-hidden="true"><circle cx="6" cy="6" r="6" fill="#fff"/><rect x="3" y="4.5" width="6" height="4" fill="var(--band-blue)"/><rect x="4" y="3" width="4" height="1.5" fill="var(--band-blue)"/></svg>
          <span>0431 587 906</span>
        </li>
        <li>
          <svg class="contact__icon" viewBox="0 0 12 12" aria-hidden="true"><circle cx="6" cy="6" r="6" fill="#fff"/><rect x="3" y="3.8" width="6" height="4.4" fill="var(--band-blue)"/><path d="M3,3.8 L6,6.2 L9,3.8" stroke="#fff" stroke-width="0.7" fill="none"/></svg>
          <span class="lower">corwin@kiteloftdev.example</span>
        </li>
        <li>
          <svg class="contact__icon" viewBox="0 0 12 12" aria-hidden="true"><circle cx="6" cy="6" r="6" fill="#fff"/><circle cx="6" cy="6" r="3.2" fill="none" stroke="var(--band-blue)" stroke-width="0.9"/><path d="M2.8,6 H9.2 M6,2.8 V9.2" stroke="var(--band-blue)" stroke-width="0.7"/></svg>
          <span class="lower">www.kiteloftdev.example</span>
        </li>
      </ul>
    </div>
  </section>

</main>
</body>
</html>
```